Corportate Power Point Template

We need a corporate PPT Design for our startup Big Data company.

Basically, our company will ingest, analyze and generate dynamic Dashboards with data consumed from different sources like Social Networks, Enterprise Legacy Systems such as e-Commerce, ERP, CRM and others.

Company is headquartered in Brazil, but will have a global presence.

Industry/Entity Type

It Company

```html
<!DOCTYPE html>
<html lang="en">
<head>
<meta charset="utf-8">
<title>Project Title Here</title>
<link href="https://fonts.googleapis.com/css2?family=Open+Sans:wght@600;700&family=Roboto+Condensed:wght@400&display=swap" rel="stylesheet">
<style>
  :root {
    --orange: #f26522;
    --ink: #1f1f1f;
    --text: #333333;
    --rule: #f6b98f;
    --header-top: #fff7f0;
    --header-bottom: #fde9d9;
    --page: #fffaf6;
    --footer: #ffffff;
    --axis: #222222;
    --brand: #3a3a3a;
  }
  * { margin: 0; padding: 0; box-sizing: border-box; }
  html, body { width: 1200px; height: 900px; overflow: hidden; }
  body { background: var(--page); font-family: "Roboto Condensed", "Arial Narrow", sans-serif; color: var(--text); }
  .slide { position: relative; width: 1200px; height: 900px; overflow: hidden;
    background: radial-gradient(ellipse at 20% 35%, #fdeee2 0%, var(--page) 55%); }
  .slide-header { position: absolute; left: 0; top: 0; width: 1200px; height: 105px;
    background: linear-gradient(180deg, var(--header-top), var(--header-bottom));
    border-bottom: 2px solid var(--rule); }
  .slide-title { position: absolute; left: 33px; top: 24px; font-family: "Open Sans", Arial, sans-serif;
    font-weight: 700; font-size: 46px; letter-spacing: -0.5px; color: var(--ink); line-height: 1.2; }
  .slide-title .accent { color: var(--orange); }
  .header-texture { position: absolute; right: 18px; top: 6px; width: 110px; height: 96px;
    background: radial-gradient(circle, rgba(242,101,34,0.13) 0%, rgba(242,101,34,0) 70%); }
  .lead { position: absolute; left: 49px; top: 168px; font-size: 25px; color: var(--text); }
  .chart { position: absolute; left: 0; top: 0; }
  .y-label, .x-label { position: absolute; font-size: 19px; color: var(--ink); white-space: nowrap; }
  .y-label { left: 56px; transform: translateY(-50%); }
  .x-label { top: 717px; transform: translateX(-50%); }
  .slide-footer { position: absolute; left: 0; top: 807px; width: 1200px; height: 93px;
    background: linear-gradient(180deg, var(--footer), #f7f2ee); border-top: 2px solid var(--rule); }
  .brand { position: absolute; left: 20px; top: 24px;
    font-family: "Open Sans", Arial, sans-serif; font-weight: 600; font-size: 36px; line-height: 1.2; color: var(--brand); }
  .presenter { position: absolute; right: 17px; top: 36px; font-size: 20px; color: var(--ink); }
  .presenter .name { color: var(--orange); }
</style>
</head>
<body>
<main class="slide">
  <header class="slide-header">
    <h1 class="slide-title"><span class="accent">Project</span> Title Here</h1>
    <div class="header-texture" role="img" aria-label="Faint decorative tile texture"></div>
  </header>

  <p class="lead">Lorem ipsum dolor sit ipsum Lorem ipsum dolor sit ipsum Lorem ipsum Lorem ipsum</p>

  <svg class="chart" width="1200" height="900" viewBox="0 0 1200 900" aria-label="Bar chart">
    <rect x="259.5" y="553.5" width="49.5" height="142.5" fill="#8a8a8a"/>
    <rect x="319.5" y="439.5" width="63" height="256.5" fill="#f5834b"/>
    <rect x="397.5" y="484.5" width="60" height="211.5" fill="#e8926a"/>
    <rect x="471" y="570" width="60" height="126" fill="#f8bd70"/>
    <rect x="549" y="658.5" width="66" height="37.5" fill="#f26f33"/>
    <rect x="627" y="684" width="75" height="12" fill="#808080"/>
    <rect x="711" y="294" width="61.5" height="402" fill="#f5834b"/>
    <rect x="786" y="655.5" width="66" height="40.5" fill="#f56f3c"/>
    <rect x="864" y="676.5" width="64.5" height="19.5" fill="#f7a238"/>
    <line x1="259.5" y1="255" x2="259.5" y2="696" stroke="var(--axis)" stroke-width="1.5"/>
    <line x1="259.5" y1="696" x2="1018.5" y2="696" stroke="var(--axis)" stroke-width="1.5"/>
  </svg>

  <span class="y-label" style="top:280px">Lorem ipsum text here</span>
  <span class="y-label" style="top:342px">Lorem ipsum text here</span>
  <span class="y-label" style="top:403px">Lorem ipsum text here</span>
  <span class="y-label" style="top:480px">Lorem ipsum text here</span>
  <span class="y-label" style="top:546px">Lorem ipsum text here</span>
  <span class="y-label" style="top:622px">Lorem ipsum text here</span>
  <span class="y-label" style="top:688px">Lorem ipsum text here</span>

  <span class="x-label" style="left:345px">Lorem ipsum text here</span>
  <span class="x-label" style="left:633px">Lorem ipsum text here</span>
  <span class="x-label" style="left:932px">Lorem ipsum text here</span>

  <footer class="slide-footer">
    <p class="brand">Novarra Data</p>
    <p class="presenter">Persentatator Name : <span class="name">Marina Costa</span></p>
  </footer>
</main>
</body>
</html>
```